SkyvoTrade - where frequent flyers can cash out their airline miles

SkyvoTrade enable the trade of airline miles between individuals. Our landing page which I want to redesign should refer to individuals who have miles in airline loyalty programs and would like to sell them with our platform

I would like to get a landing page design with a look and feel much more advanced and appealing then the one we currently have.

Page should include the information and fields in our current landing page but should be more professional and include except for the current two partner's logos and our logo of course, also the attached banner of staynestly.example with a link to staynestly.example with our affiliate code.

Audience of our web page is business men and heavy travellers therefore, page should reflect professionalism and should be business wise. There could be something that has to do with airplanes and money in terms of the background and pictures shows.

Additional text (on top of the short description at skyvotrade.example is -
"
SkyvoTrade™ converts frequent flyers' accumulated miles to exceptionally low-priced flight tickets. It serves as an online trading platform for sellers of miles and buyers of flight tickets, offering airline customers a fully automated process whereby flight tickets are created out of loyalty club miles.
"

Our web site as a reference is www.skyvotrade.example

Target Market(s)

Business men who are heavily travellers

Industry/Entity Type

Travel Industry

Number of Pages Required

1 page

Font styles to use
Sans Serif

Colors
85acd3
0255a3

Requirements
Must have
• Our logo and the 3 logos mentioned at the description. It should have on the top the look & Feel that it currently has on our landing page - www.skyvotrade.example
Nice to have
• I would like people entering the web page to love it and for them to leave the relevant details so we get back to them
Should not have
• Not too many texts or images. Don't want people to scroll down too much if at all

```html
<!DOCTYPE html>
<html lang="en">
<head>
<meta charset="utf-8">
<title>SkyvoTrade – Loyalty Pays</title>
<link href="https://fonts.googleapis.com/css2?family=Roboto+Condensed:wght@300;400;700&display=swap" rel="stylesheet">
<style>
:root{
  --blue:#0255a3;
  --sky:#85acd3;
  --orange:#f08a0b;
  --ink:#222;
  --grey:#555;
  --footer:#333;
  --footer-text:#9a9a9a;
  --panel:rgba(70,75,85,.72);
}
*{margin:0;padding:0;box-sizing:border-box}
html,body{width:1200px;height:1094px;overflow:hidden}
body{font-family:"Roboto Condensed",sans-serif;color:var(--ink);background:#fff;position:relative}
.abs{position:absolute}

.site-header{position:absolute;left:0;top:0;width:1200px;height:101px;background:linear-gradient(#fbfbef,#ececec)}
.brand{left:99px;top:16px}
.brand-name{font-size:40px;font-weight:700;color:#111;line-height:1;letter-spacing:-.5px}
.brand-tag{font-size:13px;font-weight:700;color:#111;text-align:right;margin-top:8px}
.nav a{position:absolute;top:33px;height:35px;line-height:35px;font-size:16px;color:#111;text-decoration:none}
.nav .active{background:var(--blue);color:#fff;padding:0 13px;border-radius:2px}
.contact{top:26px;display:flex;align-items:center;gap:7px;font-size:16px;color:#222}
.contact .ring{width:42px;height:42px;border:1.5px solid #111;border-radius:50%;display:flex;align-items:center;justify-content:center}

.hero{left:0;top:101px;width:1200px;height:511px;background:linear-gradient(180deg,#7fb8e6 0%,#bfe0f2 40%,#2fb3b8 66%,#d8bf93 74%,#c9a877 100%)}
.arrow{top:250px}
.search-panel{left:294px;top:136px;width:612px;height:423px;background:var(--panel);color:#fff;border-radius:2px}
.search-panel h1{position:absolute;left:29px;top:24px;font-size:26px;font-weight:400;display:flex;align-items:center;gap:10px}
.search-panel .lead{position:absolute;left:31px;top:66px;font-size:11px}
.label{position:absolute;font-size:15px;font-weight:400}
.field{position:absolute;background:#fff;border-radius:2px;color:#666;font-size:11.5px;padding-left:14px;display:flex;align-items:center}
.field.date{width:103px;height:38px;justify-content:space-between;padding-right:10px}
.check{position:absolute;left:31px;top:295px;display:flex;align-items:center;gap:10px;font-size:15px}
.check span.box{width:16px;height:15px;background:#fff}
.radios{position:absolute;left:29px;top:332px;display:flex;gap:20px;font-size:15px}
.radios label{display:flex;align-items:center;gap:10px}
.radios i{width:10px;height:10px;border-radius:50%;background:#fff;display:block}
.btn-search{position:absolute;left:27px;top:362px;width:119px;height:38px;background:var(--orange);color:#fff;font-size:15px;line-height:38px;text-align:center;border-radius:2px}

.welcome{left:99px;top:652px;width:668px}
.welcome h2{font-size:26px;font-weight:400;color:var(--blue)}
.welcome p{margin-top:19px;font-size:15.5px;font-weight:300;line-height:20.6px;color:var(--grey);text-align:justify}
.btn-book{position:absolute;left:100px;top:789px;width:126px;height:46px;background:var(--blue);color:#fff;font-size:20px;font-weight:700;line-height:46px;text-align:center;border-radius:2px}
.partner{top:886px;display:flex;align-items:center;gap:10px;font-size:26px;color:#445}
.partner .mark{width:84px;height:78px;background:#4f6472;border-radius:6px}
.partner.second{color:#d41a1a;font-weight:700;font-size:34px}
.promo{left:800px;top:659px;width:300px;height:301px;background:linear-gradient(180deg,#0d4aa0 0%,#0d4aa0 26%,#8fcff0 34%,#eae4d4 60%,#35b7e0 80%,#1a80c8 100%);color:#fff;text-align:center}
.promo h3{font-size:24px;font-weight:400;margin-top:14px}
.promo .sub{font-size:16px;margin-top:2px}
.promo .cta{position:absolute;left:98px;top:212px;width:104px;height:40px;background:var(--blue);border:2px solid #fff;font-size:18px;line-height:36px}
.promo .promo-brand{position:absolute;left:0;right:0;top:260px;font-size:20px;font-weight:700}

.site-footer{left:0;top:1000px;width:1200px;height:94px;background:var(--footer);color:var(--footer-text);font-size:12px}
.footer-nav{position:absolute;left:98px;top:30px;display:flex;gap:26px}
.copy{position:absolute;left:99px;top:56px}
.social{position:absolute;left:1011px;top:33px;display:flex;gap:14px}
.social span{width:22px;height:22px;background:#8a8a8a;border-radius:3px}
</style>
</head>
<body>

<header class="site-header">
  <div class="abs brand">
    <div class="brand-name">SkyvoTrade</div>
    <div class="brand-tag">Loyalty Pays</div>
  </div>
  <nav class="nav">
    <a class="active" style="left:315px">HOME</a>
    <a style="left:396px">ABOUT</a>
    <a style="left:473px">SERVICES</a>
    <a style="left:568px">BOOKING</a>
    <a style="left:659px">CONTACT US</a>
  </nav>
  <div class="abs contact" style="left:767px">
    <span class="ring"><svg width="18" height="18" viewBox="0 0 24 24"><path fill="#111" d="M6.6 10.8a15 15 0 0 0 6.6 6.6l2.2-2.2c.3-.3.7-.4 1-.2 1.1.4 2.3.6 3.6.6.6 0 1 .4 1 1V20c0 .6-.4 1-1 1A17 17 0 0 1 3 4c0-.6.4-1 1-1h3.5c.6 0 1 .4 1 1 0 1.3.2 2.5.6 3.6.1.3 0 .7-.2 1z"/></svg></span>
    1800 555 019
  </div>
  <div class="abs contact" style="left:922px">
    <span class="ring"><svg width="18" height="14" viewBox="0 0 24 18"><path fill="#111" d="M0 2h24v14H0zM2 3l10 7 10-7z"/><path fill="#fff" d="M2 3.5l10 7 10-7" stroke="#fff" stroke-width="1.5"/></svg></span>
    hello@skyvotrade.example
  </div>
</header>

<section class="abs hero" role="img" aria-label="Sunny beach with straw umbrellas and sun loungers by the sea">
  <svg class="abs arrow" style="left:45px" width="16" height="30" viewBox="0 0 16 30"><path d="M15 1L2 15l13 14" fill="none" stroke="#333" stroke-width="1.5"/></svg>
  <svg class="abs arrow" style="left:1133px" width="16" height="30" viewBox="0 0 16 30"><path d="M1 1l13 14L1 29" fill="none" stroke="#333" stroke-width="1.5"/></svg>
</section>

<form class="abs search-panel">
  <h1><svg width="24" height="24" viewBox="0 0 24 24"><circle cx="10" cy="10" r="7" fill="none" stroke="#fff" stroke-width="3"/><path d="M15 15l7 7" stroke="#fff" stroke-width="3.5" stroke-linecap="round"/></svg>FIND THE BEST DEALS</h1>
  <p class="lead">20 MILLION ROOMS ARE AT YOUR FINGERTIPS – WHICH ONE WILL YOU CHOOSE?</p>
  <span class="label" style="left:30px;top:107px">DESTINATION/HOTEL NAME:</span>
  <div class="field" style="left:29px;top:140px;width:552px;height:48px">Country, City, District or Landmark</div>
  <span class="label" style="left:30px;top:210px">CHECK-IN DATE</span>
  <span class="label" style="left:261px;top:210px">CHECK-IN DATE</span>
  <div class="field date" style="left:28px;top:239px">Day<svg width="12" height="12" viewBox="0 0 12 12"><rect x="0.5" y="1.5" width="11" height="10" fill="none" stroke="#555"/><path d="M0 4h12M3 0v3M9 0v3M3 6h1M6 6h1M9 6h1M3 9h1M6 9h1M9 9h1" stroke="#555"/></svg></div>
  <div class="field date" style="left:140px;top:239px">Month<svg width="12" height="12" viewBox="0 0 12 12"><rect x="0.5" y="1.5" width="11" height="10" fill="none" stroke="#555"/><path d="M0 4h12M3 0v3M9 0v3M3 6h1M6 6h1M9 6h1M3 9h1M6 9h1M9 9h1" stroke="#555"/></svg></div>
  <div class="field date" style="left:260px;top:239px">Day<svg width="12" height="12" viewBox="0 0 12 12"><rect x="0.5" y="1.5" width="11" height="10" fill="none" stroke="#555"/><path d="M0 4h12M3 0v3M9 0v3M3 6h1M6 6h1M9 6h1M3 9h1M6 9h1M9 9h1" stroke="#555"/></svg></div>
  <div class="field date" style="left:371px;top:239px">Month<svg width="12" height="12" viewBox="0 0 12 12"><rect x="0.5" y="1.5" width="11" height="10" fill="none" stroke="#555"/><path d="M0 4h12M3 0v3M9 0v3M3 6h1M6 6h1M9 6h1M3 9h1M6 9h1M9 9h1" stroke="#555"/></svg></div>
  <div class="check"><span class="box"></span>I'M NOT READY TO ENTER DATES</div>
  <div class="radios"><label><i></i>WORK</label><label><i></i>LEISURE</label></div>
  <div class="btn-search">SEARCH NOW</div>
</form>

<section class="abs welcome">
  <h2>WELCOME TO SKYVOTRADE</h2>
  <p>SkyvoTrade™ converts frequent flyers’ accumulated miles to exceptionally low-priced flight tickets. It serves as an online trading platform for sellers of miles and buyers of flight tickets, offering airline customers a fully automated process whereby flight tickets are created out of loyalty club miles.</p>
</section>
<div class="btn-book">BOOK NOW</div>

<div class="abs partner" style="left:99px"><span class="mark"></span>Brightlane</div>
<div class="abs partner second" style="left:300px;top:900px">Corvella Tours</div>

<aside class="abs promo" role="img" aria-label="Promotional banner with a tropical beach and straw umbrellas">
  <h3>Vacation of a Lifetime</h3>
  <div class="sub">Book a slice of paradise</div>
  <div class="cta">Book now</div>
  <div class="promo-brand">staynestly.example</div>
</aside>

<footer class="abs site-footer">
  <div class="footer-nav"><span>Home</span><span>About</span><span>Services</span><span>Booking</span><span>Contact Us</span></div>
  <div class="copy">© 2015 skyvotrade.example. All rights reserved.</div>
  <div class="social"><span></span><span></span><span></span></div>
</footer>

</body>
</html>
```